KVM Contracting services . Building and maintenance services, optic fibre installation

Business cards and logo design.I need a logo that I can use on business cards ,workwear and on my vehicles. I would like the KVM to be the main or larger text and contracting services to be the smaller or less important text.I like monograms, modern designs and repeating patterns symbols. I am also a Gemini and my favourite number is 22 so if this can be any inspiration to help with the design. Am thinking of the using German flag colours as a his is my family’s heritage. And the other 2 main colours I wear is black and white.But any ideas are appreciated.I do not need a design that is trade specific but a design that could be used for any business.

Target Market(s)

General public

Contact Information for Business Card

KVM Contracting Services ( front of business card)

(Back of business card)
Darren Holtwick
0451907326
Maintenance services
Optic fibre and data installation

Logo Text

Logo can just be pattern or monogram or incorporate KVM . I like the gemini star sign and the number 22

Colors
ec1f27
000000
fbee3e
ffffff

Requirements
Must have
• Logo and KVM Contracting Services on the front of business card
Nice to have
• Possible use of German flag colours.
• Modern design.
• Design to be able to be used on black or white background as I want to put it on clothing

```html
<!DOCTYPE html>
<html lang="en">
<head>
<meta charset="utf-8">
<title>KVM Contracting Services — Business Card</title>
<link rel="stylesheet" href="https://fonts.googleapis.com/css2?family=Roboto:wght@700;900&family=Roboto+Condensed:wght@700&family=Open+Sans:wght@400&display=swap">
<style>
  :root {
    --backdrop: #2a2a2c;
    --card: #1c1c1e;
    --brand-red: #ec1f27;
    --white: #ffffff;
    --rule: #5a5a5c;
    --pattern-top: #2b2b2d;
    --pattern-bottom: #1c1c1e;
    --silver: #c9c9cb;
  }
  * { box-sizing: border-box; margin: 0; padding: 0; }
  html, body { width: 1200px; height: 1108px; overflow: hidden; }
  body {
    background: var(--backdrop);
    display: flex;
    align-items: center;
    justify-content: center;
    gap: 60px;
  }
  .card {
    width: 420px;
    height: 680px;
    background: var(--card);
    border-radius: 24px;
    position: relative;
    overflow: hidden;
    box-shadow: 0 20px 40px rgba(0,0,0,0.45);
  }
  /* Front */
  .card-front { display: flex; flex-direction: column; align-items: center; }
  .brand {
    margin-top: 150px;
    display: flex;
    align-items: center;
    gap: 18px;
  }
  .brand-dot {
    width: 64px; height: 64px;
    border-radius: 50%;
    background: var(--brand-red);
    flex: none;
  }
  .brand-text { display: flex; flex-direction: column; }
  .brand-name {
    font-family: "Roboto", sans-serif;
    font-weight: 900;
    font-size: 84px;
    line-height: 0.9;
    letter-spacing: 10px;
    color: var(--brand-red);
  }
  .brand-tagline {
    font-family: "Roboto Condensed", sans-serif;
    font-weight: 700;
    font-size: 17px;
    letter-spacing: 0.5px;
    color: var(--white);
    text-transform: uppercase;
  }
  .contact { margin-top: 110px; text-align: center; width: 300px; }
  .contact-name {
    font-family: "Roboto Condensed", sans-serif;
    font-weight: 700;
    font-size: 28px;
    color: var(--brand-red);
    text-transform: uppercase;
  }
  .contact-phone {
    font-family: "Open Sans", sans-serif;
    font-size: 28px;
    letter-spacing: 1px;
    color: var(--white);
    margin-top: 2px;
  }
  .contact-rule {
    border: 0;
    border-top: 1px solid var(--rule);
    margin: 14px 0 20px;
  }
  .services {
    font-family: "Open Sans", sans-serif;
    font-size: 20px;
    line-height: 1.15;
    color: var(--white);
    text-transform: uppercase;
    list-style: none;
  }
  /* Back */
  .pattern-field {
    position: absolute;
    inset: 0 0 200px 0;
    background: linear-gradient(180deg, var(--pattern-top), var(--pattern-bottom));
  }
  .back-brand {
    position: absolute;
    right: 40px;
    bottom: 80px;
    text-align: right;
    color: var(--silver);
  }
  .back-brand .brand-name {
    color: var(--silver);
    font-size: 124px;
    letter-spacing: 14px;
  }
  .back-brand .brand-tagline {
    color: var(--silver);
    font-size: 25px;
    margin-top: 4px;
  }
</style>
</head>
<body>
  <section class="card card-front" aria-label="Business card front">
    <div class="brand">
      <span class="brand-dot"></span>
      <div class="brand-text">
        <span class="brand-name">KVM</span>
        <span class="brand-tagline">Contracting Services</span>
      </div>
    </div>
    <div class="contact">
      <p class="contact-name">Darren Holtwick</p>
      <p class="contact-phone">0451907326</p>
      <hr class="contact-rule">
      <ul class="services">
        <li>Maintenance Services</li>
        <li>Optic Fibre and Data</li>
        <li>Installation</li>
      </ul>
    </div>
  </section>

  <section class="card card-back" aria-label="Business card back">
    <div class="pattern-field" role="img" aria-label="Faint repeating brand pattern in dark grey fading downward"></div>
    <div class="back-brand">
      <div class="brand-name">KVM</div>
      <div class="brand-tagline">Contracting Services</div>
    </div>
  </section>
</body>
</html>
```